New Business Card Design

We would like to refresh our business cards and make them look better. We are an IT company specialising in Cloud Services, IT Managed Services, software and hardware. I have attached a PSD of our current design. Also attached our logo.
Updates

I have uploaded all new logos in EPS format.

Can you please edit all designs to include a job title for Marcus Hollis, eg. General Manager

Industry/Entity Type

Software

Colors
ffffff

Requirements
Must have
• Please use white background.
Should not have
• Black background

```html
<!DOCTYPE html>
<html lang="en">
<head>
<meta charset="utf-8">
<title>Clarity Systems – Business Card</title>
<link href="https://fonts.googleapis.com/css2?family=Open+Sans:wght@400;600;700&display=swap" rel="stylesheet">
<style>
  :root {
    --canvas: #e6e6ee;
    --card: #ffffff;
    --slate: #838e99;
    --brand-red: #c0392b;
    --ink: #2b2b2b;
    --ink-soft: #444a50;
    --faint: #f3f0f0;
  }
  * { box-sizing: border-box; margin: 0; padding: 0; }
  html, body {
    width: 1200px; height: 987px; overflow: hidden;
    background: var(--canvas);
    font-family: "Open Sans", Arial, sans-serif;
  }
  .sheet { position: relative; width: 1200px; height: 987px; }
  .card {
    position: absolute; left: 230px; width: 740px; height: 423px;
    background: var(--card); border-radius: 26px; overflow: hidden;
    box-shadow: 0 6px 18px rgba(0,0,0,.12);
  }
  .card--back { top: 48px; }
  .card--front { top: 516px; }

  .brand { display: flex; align-items: center; gap: 18px; }
  .brand__dot {
    width: 58px; height: 58px; border-radius: 50%;
    background: var(--brand-red); flex: none;
  }
  .brand__name {
    font-weight: 400; color: var(--ink); letter-spacing: 0.16em;
    font-size: 40px; line-height: 1; white-space: nowrap;
  }

  /* back */
  .card--back .brand { position: absolute; left: 150px; top: 70px; }
  .tagline {
    position: absolute; left: 0; right: 0; top: 190px; text-align: center;
    font-size: 24px; line-height: 1.45; color: var(--ink-soft);
  }
  .web-line {
    position: absolute; left: 0; right: 0; top: 300px; text-align: center;
    font-size: 19px; letter-spacing: 0.32em; color: var(--ink-soft);
  }
  .web-line__host { color: var(--brand-red); font-weight: 600; }

  /* front */
  .card__art { position: absolute; inset: 0; }
  .card--front .brand { position: absolute; left: 40px; top: 112px; gap: 14px; }
  .card--front .brand__dot { width: 40px; height: 40px; }
  .card--front .brand__name { font-size: 26px; letter-spacing: 0.1em; }
  .contact {
    position: absolute; left: 42px; top: 214px; list-style: none;
    font-size: 17px; color: var(--ink); line-height: 1.6;
  }
  .contact li { display: flex; align-items: center; gap: 10px; }
  .contact svg { width: 15px; height: 15px; flex: none; }
  .person {
    position: absolute; right: 28px; top: 212px; text-align: right; color: #fff;
  }
  .person__name { font-size: 22px; font-weight: 700; line-height: 1.3; }
  .person__role { font-size: 16px; font-weight: 400; }
  .watermark-dot {
    position: absolute; left: 380px; top: 292px; width: 90px; height: 90px;
    border-radius: 50%; background: var(--faint);
  }
</style>
</head>
<body>
<main class="sheet">

  <section class="card card--back" aria-label="Business card back">
    <div class="brand">
      <span class="brand__dot"></span>
      <span class="brand__name">Clarity Systems</span>
    </div>
    <p class="tagline">We are an IT company specializing in Cloud Services<br>IT Managed Services, software and hardware</p>
    <p class="web-line">www.<span class="web-line__host">claritysys</span>.com.au</p>
  </section>

  <section class="card card--front" aria-label="Business card front">
    <svg class="card__art" viewBox="0 0 740 423" aria-hidden="true">
      <path d="M0 0 L0 40 C380 40 520 180 560 423 L740 423 L740 0 Z" fill="var(--slate)"/>
      <path d="M0 40 C380 40 520 180 560 423" fill="none" stroke="var(--brand-red)" stroke-width="12"/>
    </svg>
    <span class="watermark-dot"></span>
    <div class="brand">
      <span class="brand__dot"></span>
      <span class="brand__name">Clarity Systems</span>
    </div>
    <ul class="contact">
      <li><svg viewBox="0 0 16 16"><circle cx="8" cy="8" r="8" fill="var(--brand-red)"/><path d="M5 4l2 2-1 1.5 2.5 2.5L10 9l2 2-1.5 1.5C7 12 4 9 3.5 5.5Z" fill="#fff"/></svg>07 3200 4815</li>
      <li><svg viewBox="0 0 16 16"><rect x="4" y="1" width="8" height="14" rx="2" fill="var(--brand-red)"/><rect x="5.5" y="3" width="5" height="7" fill="#fff"/></svg>0400 123 567</li>
      <li><svg viewBox="0 0 16 16"><rect x="1" y="3" width="14" height="10" rx="1.5" fill="var(--brand-red)"/><path d="M1.5 4l6.5 5 6.5-5" fill="none" stroke="#fff" stroke-width="1.4"/></svg>mhollis@claritysys.com.au</li>
      <li><svg viewBox="0 0 16 16"><circle cx="8" cy="8" r="7" fill="var(--brand-red)"/><path d="M1 8h14M8 1c-3 3-3 11 0 14M8 1c3 3 3 11 0 14" fill="none" stroke="#fff" stroke-width="1"/></svg>www.claritysys.com.au</li>
    </ul>
    <div class="person">
      <p class="person__name">Marcus Hollis</p>
      <p class="person__role">General Manager</p>
    </div>
  </section>

</main>
</body>
</html>
```